Residential Remodeling Contractor needs updated business card

I need a new design for my business card.
Name of the company is Ridgefell Construction. I need a card that commands presence, strength, integrity. I have been in business for 28 years. I am a Residential Remodeling Contractor that covers all aspects of a residential remodel and build.

```html
<!DOCTYPE html>
<html lang="en">
<head>
<meta charset="utf-8">
<title>Ridgefell Construction – Business Card</title>
<link rel="stylesheet" href="https://fonts.googleapis.com/css2?family=Crimson+Text:wght@700&family=Arimo:wght@400&display=swap">
<style>
  :root {
    --navy: #173d7a;
    --ink: #444444;
    --paper: #ffffff;
    --backdrop: #9a9a9a;
    --serif: "Crimson Text", Georgia, serif;
    --sans: "Arimo", Arial, sans-serif;
  }
  * { box-sizing: border-box; margin: 0; padding: 0; }
  html, body { width: 1200px; height: 1059px; overflow: hidden; }
  body { background: var(--backdrop); position: relative; font-family: var(--sans); }

  .card {
    position: absolute;
    width: 690px;
    height: 392px;
    border-radius: 24px;
    overflow: hidden;
  }
  .card--front { left: 256px; top: 89px; background: var(--paper); }
  .card--back { left: 254px; top: 569px; background: var(--navy); }

  .wordmark {
    position: absolute;
    display: flex;
    align-items: center;
    font-family: var(--sans);
    font-weight: 400;
    line-height: 1.1;
  }
  .wordmark__mark { flex: none; }
  .wordmark__name span { display: block; }

  .card--front .wordmark { left: 66px; top: 164px; color: var(--navy); font-size: 30px; }
  .card--front .wordmark__mark { width: 28px; height: 28px; background: var(--navy); margin-right: 14px; }

  .card--back .wordmark { left: 150px; top: 150px; color: var(--paper); font-size: 52px; }
  .card--back .wordmark__mark { width: 48px; height: 48px; background: var(--paper); margin-right: 26px; }

  .divider {
    position: absolute;
    left: 344px; top: 119px;
    width: 1.5px; height: 150px;
    background: var(--navy);
  }

  .contact { position: absolute; left: 371px; top: 114px; }
  .contact__name {
    font-family: var(--serif);
    font-weight: 700;
    font-size: 24px;
    color: var(--navy);
    letter-spacing: 0.3px;
    line-height: 1;
  }
  .contact__role { font-size: 16px; color: var(--ink); margin-top: 4px; }
  .contact__list { list-style: none; margin-top: 22px; }
  .contact__item {
    display: flex; align-items: center;
    font-size: 16.5px; color: var(--ink);
    height: 24px;
  }
  .contact__icon { width: 13px; height: 13px; margin-right: 9px; flex: none; fill: var(--navy); }
  .contact__item .accent { color: var(--navy); }

  .address-band {
    position: absolute; left: 0; bottom: 0;
    width: 100%; height: 40px;
    background: var(--navy);
    color: var(--paper);
    font-size: 16px;
    display: flex; align-items: center; justify-content: center;
    word-spacing: 1px;
  }
</style>
</head>
<body>
  <section class="card card--front" aria-label="Business card front">
    <div class="wordmark">
      <div class="wordmark__mark"></div>
      <div class="wordmark__name"><span>Ridgefell</span><span>Construction</span></div>
    </div>

    <div class="divider"></div>

    <div class="contact">
      <p class="contact__name">DANIEL OKAFOR</p>
      <p class="contact__role">Owner &amp; Manager</p>
      <ul class="contact__list">
        <li class="contact__item">
          <svg class="contact__icon" viewBox="0 0 16 16" aria-hidden="true"><path d="M1 6c0-2 3-3.5 7-3.5S15 4 15 6v1.5h-3.5V6c-1-.6-6-.6-7 0v1.5H1z"/><path d="M3.5 8.5 5 7h6l1.5 1.5V13h-9z"/></svg>
          555 014 2876
        </li>
        <li class="contact__item">
          <svg class="contact__icon" viewBox="0 0 16 16" aria-hidden="true"><path d="M4.5 1h7a1 1 0 0 1 1 1v12a1 1 0 0 1-1 1h-7a1 1 0 0 1-1-1V2a1 1 0 0 1 1-1zm.5 2v9h6V3zm3 10a.7.7 0 1 0 0 1.4A.7.7 0 0 0 8 13z"/></svg>
          555-019-48372
        </li>
        <li class="contact__item">
          <svg class="contact__icon" viewBox="0 0 16 16" aria-hidden="true"><path d="M1 6.5 8 2l7 4.5V14H1zm1.5 1.2v5l3.6-2.5zm11 0-3.6 2.5 3.6 2.5zM3 13h10L8 9.5z"/></svg>
          info@ridgefellconstruction.com
        </li>
        <li class="contact__item">
          <svg class="contact__icon" viewBox="0 0 16 16" aria-hidden="true"><circle cx="8" cy="8" r="7"/><path d="M4 4.5c1.5.5 2 1.5 1.5 2.5S6.5 9 7 10.5 6 13 5 13.5C3 12.5 2 10 2.5 7.5zM10 3c1 .5 1.5 2 .5 2.5S9 7 10.5 8s2 1 2.5 2c.5-2 0-5-3-7z" fill="#fff"/></svg>
          <span>www.<span class="accent">ridgefellconstruction</span>.com</span>
        </li>
      </ul>
    </div>

    <div class="address-band">P.O. Box&nbsp; Street Name Country Name AB, A5B 521</div>
  </section>

  <section class="card card--back" aria-label="Business card back">
    <div class="wordmark">
      <div class="wordmark__mark"></div>
      <div class="wordmark__name"><span>Ridgefell</span><span>Construction</span></div>
    </div>
  </section>
</body>
</html>
```